Cyber Security Site Design (Products & Consulting)

I need my website redesigned to be engaging, clean, efficient and modern. My company (when its up and running) is going to be concentrated on two things: a few specific products for cyber security as well as cyber security consulting services. The background I bring to the field is having worked with small companies all the way to the largest government organizations and advising them on their security posture and how to improve it. We need the ability to add products and services easily.

For a sample product, you can use either Tarnet (http://www.tarnet-relay.org/) or Verodyne Ashmantle (https://www.verodyne.com/products/relay-hx-and-fortified-edge-portal).

It will replace https://lumerafieldworks.com/

Target Market(s)

Cyber Security professionals in all verticals

Coding

Coded - Design and coding required

Number of Pages Required

4 page

Font styles to use
Sans Serif

Colors
6b449b

Requirements
Must have
• Ability to easily modify
• Have main page
• Have product specific pages
• Have consulting services pages
• Have executive team information
• Clean, modern design
• Usage of the logo and its color scheme
Nice to have
• I like the idea of a left collapsed sidebar (so icons only) that can expand for text.
• I am also open to a very unique landing page, possibly a shape in the middle (hexagons maybe?) with each of the options there.
Should not have
• Nothing that looks like it came out of a hacker movie

```html
<!DOCTYPE html>
<html lang="en">
<head>
<meta charset="utf-8">
<title>Lumera Fieldworks — Cyber Security Consulting &amp; Products</title>
<link rel="stylesheet" href="https://fonts.googleapis.com/css2?family=Exo+2:wght@400;500;600;700&family=Montserrat:wght@400;500;600;700&display=swap">
<style>
:root{
  --purple:#6b449b;
  --purple-dark:#54337d;
  --purple-deep:#3d2160;
  --ink:#222226;
  --text:#55555c;
  --muted:#8a8a92;
  --line:#e3e3e8;
  --bg-soft:#f3f3f5;
  --charcoal:#3a3a3f;
  --white:#ffffff;
}
*{box-sizing:border-box;margin:0;padding:0}
html,body{width:1200px;height:3846px;overflow:hidden}
body{position:relative;background:var(--white);font-family:"Montserrat",Arial,sans-serif;color:var(--text)}
.abs{position:absolute}
.brand{font-family:"Exo 2",Arial,sans-serif;font-weight:700;color:var(--purple);letter-spacing:2px;display:flex;align-items:center;gap:12px}
.brand .dot{width:34px;height:34px;border-radius:50%;background:var(--purple);flex:none}
.section-title{font-family:"Exo 2",Arial,sans-serif;font-size:44px;font-weight:400;color:var(--ink);text-align:center;letter-spacing:1px}
.section-title b{font-weight:700}
.title-rule{width:44px;height:4px;background:var(--purple);margin:16px auto 0}

/* header */
.site-header{top:0;left:0;width:1200px;height:72px;background:var(--white);display:flex;align-items:center;justify-content:space-between;padding:0 88px 0 141px}
.site-header .brand{font-size:24px}
.main-nav{display:flex;align-items:center;gap:40px;font-size:13px;font-weight:600;color:var(--ink)}
.main-nav .active{color:var(--purple)}
.btn-pill{display:inline-flex;align-items:center;gap:10px;background:var(--purple);color:var(--white);border-radius:22px;font-weight:600;font-size:13px;padding:10px 20px}
.btn-pill i{width:20px;height:20px;border-radius:50%;background:var(--white);display:block}

/* hero */
.hero{top:72px;left:0;width:1200px;height:672px;overflow:hidden}
.hero-photo{position:absolute;inset:0;background:linear-gradient(180deg,#1b2850 0%,#2d3d6a 35%,#4a4760 60%,#8a6a58 78%,#2a2436 100%)}
.hero h1{position:absolute;top:200px;width:100%;text-align:center;font-family:"Exo 2",Arial,sans-serif;font-size:48px;font-weight:600;color:var(--white);letter-spacing:1px}
.hero p{position:absolute;top:265px;width:100%;text-align:center;font-size:19px;color:var(--white)}
.hero .btn-pill{position:absolute;top:308px;left:514px;font-size:12px;padding:9px 18px}
.hero-shapes{position:absolute;left:0;top:0}
.hero-tile{position:absolute;top:530px;display:flex;align-items:center;gap:18px;font-family:"Exo 2",Arial,sans-serif;font-size:25px;font-weight:600;color:var(--white);line-height:1.15}
.hero-tile .ico{width:56px;height:56px;border-radius:50%;border:2px solid var(--white);flex:none;display:flex;align-items:center;justify-content:center}
.hero-center{position:absolute;left:562px;top:523px;width:76px;height:76px;border-radius:50%;background:var(--white);box-shadow:0 4px 14px rgba(0,0,0,.25);display:flex;align-items:center;justify-content:center}
.hero-center span{width:40px;height:40px;border-radius:50%;background:var(--purple)}

/* about */
.about-text{top:820px;left:146px;width:470px}
.about-heading{display:flex;align-items:center;gap:16px;font-family:"Exo 2",Arial,sans-serif;font-size:44px;color:var(--ink);margin-bottom:40px}
.about-heading .brand{font-size:30px}
.about-text p{font-size:12.5px;line-height:1.62;margin-bottom:16px}
.about-text p.lead{color:var(--ink);font-weight:600}
.about-text .hl{color:var(--purple);font-weight:700}
.about-text .btn-pill{margin-top:6px;padding:9px 18px;font-size:12px}
.about-frame{top:820px;left:697px;width:360px;height:436px}
.about-photo{position:absolute;left:20px;top:20px;width:320px;height:396px;border-radius:20px;background:linear-gradient(160deg,#c9ccd2,#8d939c 60%,#5f6670)}

/* services */
.services{top:1328px;left:0;width:1200px;height:582px;background:var(--bg-soft)}
.services .section-title{padding-top:60px}
.services .intro{width:840px;margin:36px auto 0;text-align:center;font-size:12.5px;line-height:1.6}
.services .intro .lead{color:var(--ink);font-weight:600;margin-bottom:12px}
.services .intro .hl{color:var(--purple);font-weight:700}
.service-row{position:absolute;top:300px;left:141px;width:915px;height:218px;display:flex;background:var(--white);box-shadow:0 2px 12px rgba(0,0,0,.06)}
.service-card{flex:1;text-align:center;padding:26px 14px 0;border-right:1px solid var(--line);position:relative}
.service-card:last-child{border-right:none}
.service-card svg{width:48px;height:48px;stroke:var(--purple);fill:none;stroke-width:2}
.service-card h3{font-family:"Montserrat",Arial,sans-serif;font-size:13px;font-weight:600;color:var(--ink);margin:16px 0 10px;line-height:1.3}
.service-card p{font-size:11px;line-height:1.45;color:var(--muted)}
.service-card.is-active{background:var(--purple);margin-top:-14px;margin-bottom:-20px;border-radius:14px 14px 0 0;border:none}
.service-card.is-active svg{stroke:var(--white)}
.service-card.is-active h3,.service-card.is-active p{color:var(--white)}
.service-card .more{display:block;margin-top:12px;font-size:11px;font-weight:600;color:var(--white)}
.slider-arrow{position:absolute;top:391px;width:34px;height:34px;border-radius:50%;background:var(--white);box-shadow:0 1px 6px rgba(0,0,0,.15);display:flex;align-items:center;justify-content:center}

/* products */
.products{top:1910px;left:0;width:1200px;height:744px}
.products .section-title{padding-top:62px}
.product-wheel{position:absolute;left:0;top:0}
.product-label{position:absolute;font-size:14px;font-weight:600;color:var(--ink);line-height:1.3}
.product-label.is-featured{color:var(--purple)}

/* team */
.team{top:2654px;left:0;width:1200px;height:641px;background:var(--bg-soft)}
.team .section-title{padding-top:66px}
.team-card{position:absolute;top:179px;width:262px;height:348px;background:var(--white);border-radius:22px;overflow:hidden;box-shadow:0 4px 16px rgba(0,0,0,.08);text-align:center}
.team-photo{height:218px;background:linear-gradient(180deg,#d9dde2,#9aa1aa)}
.team-card h4{font-size:15px;font-weight:700;color:var(--ink);margin-top:34px}
.team-card .role{font-size:11px;color:var(--muted);margin-top:4px}
.team-card.is-open{background:var(--purple);height:348px}
.team-card.is-open .team-photo{height:190px}
.team-card.is-open h4,.team-card.is-open .role,.team-card.is-open .contact{color:var(--white)}
.team-card.is-open h4{margin-top:22px}
.team-card .contact{display:flex;align-items:center;justify-content:center;gap:8px;font-size:14px;font-weight:600;margin-top:14px}
.team-card .contact.small{font-size:11px;font-weight:500;margin-top:8px}

/* footer */
.site-footer{top:3295px;left:0;width:1200px;height:551px}
.footer-band{position:absolute;left:0;top:0}
.site-footer .brand{position:absolute;top:20px;left:0;width:1200px;justify-content:center;color:var(--white);font-size:30px}
.site-footer .brand .dot{background:var(--white)}
.cta{position:absolute;top:112px;left:138px;width:440px;color:var(--white)}
.cta h2{font-family:"Exo 2",Arial,sans-serif;font-size:34px;font-weight:600;letter-spacing:1px}
.cta h2 + .rule{width:42px;height:3px;background:var(--white);margin:8px 0 14px}
.cta p{font-size:12.5px;line-height:1.5}
.footer-cols{position:absolute;top:254px;left:138px;display:flex;gap:56px;color:var(--white)}
.footer-cols h5{font-size:13px;font-weight:600;margin-bottom:16px}
.footer-cols li{list-style:none;font-size:11px;line-height:1.6}
.contact-line{display:flex;gap:10px;margin-bottom:12px;font-size:11px;line-height:1.45}
.contact-line.phone{font-size:18px;font-weight:700}
.quick-links li::before{content:"›";margin-right:8px}
.contact-form{position:absolute;top:115px;left:615px;width:442px;height:385px;background:var(--white);padding:30px 36px}
.field{height:38px;border:1px solid var(--line);margin-bottom:13px;padding:0 10px;display:flex;align-items:center;font-size:11px;color:var(--muted)}
.field.tall{height:58px;align-items:flex-start;padding-top:10px}
.contact-form .btn-pill{padding:8px 16px;font-size:12px}
.copyright{position:absolute;left:0;top:500px;width:1200px;height:51px;background:var(--purple-deep);display:flex;align-items:center;justify-content:space-between;padding:0 138px;color:#d6cbe6;font-size:11px}
.copyright b{color:var(--white)}
.socials{display:flex;gap:8px}
.socials span{width:28px;height:28px;border-radius:50%;border:1.5px solid #d6cbe6}
</style>
</head>
<body>

<header class="site-header abs">
  <div class="brand"><span class="dot"></span>LUMERA FIELDWORKS</div>
  <nav class="main-nav">
    <span class="active">HOME</span><span>ABOUT</span><span>OUR TEAM</span><span>OUR PRODUCTS</span><span>SERVICES</span>
    <span class="btn-pill"><i></i>CONTACT US</span>
  </nav>
</header>

<section class="hero abs">
  <div class="hero-photo" role="img" aria-label="Night city skyline with light trails on a highway"></div>
  <h1>CYBER SECURITY CONSULTING &amp; PRODUCTS</h1>
  <p>A full range of Cyber Security Consulting Services and Products to meet your business requirements</p>
  <span class="btn-pill"><i></i>GET STARTED NOW!</span>
  <svg class="hero-shapes" width="1200" height="672" viewBox="0 0 1200 672">
    <polygon points="0,490 600,608 600,672 0,672" fill="#6b449b"/>
    <polygon points="1200,490 600,608 600,672 1200,672" fill="#3a3a3f"/>
    <polygon points="0,642 600,672 0,672" fill="#fff"/>
    <polygon points="1200,642 600,672 1200,672" fill="#fff"/>
  </svg>
  <div class="hero-tile" style="left:140px">
    <span class="ico"><svg width="28" height="28" viewBox="0 0 24 24" fill="none" stroke="#fff" stroke-width="2"><circle cx="9" cy="8" r="3"/><path d="M3 20c0-4 3-6 6-6s6 2 6 6M15 4h6v5h-4l-2 2z"/></svg></span>
    <span>CYBER SECURITY<br>CONSULTING SERVICES</span>
  </div>
  <div class="hero-tile" style="left:790px;text-align:right">
    <span>CYBER SECURITY<br>PRODUCTS</span>
    <span class="ico"><svg width="28" height="28" viewBox="0 0 24 24" fill="none" stroke="#fff" stroke-width="2"><rect x="3" y="4" width="18" height="16" rx="2"/><path d="M3 9h18M9 13h6"/></svg></span>
  </div>
  <div class="hero-center"><span></span></div>
</section>

<section class="about-text abs">
  <div class="about-heading">ABOUT <span class="brand"><span class="dot"></span>LUMERA FIELDWORKS</span></div>
  <p class="lead"><span class="hl">LUMERA FIELDWORKS:</span> It is a long established fact that a reader will be distracted by the readable content of a page when looking at its layout. The point of using Lorem Ipsum</p>
  <p>It is a long established fact that a reader will be distracted by the readable content of a page when looking at its layout. The point of using Lorem Ipsum is that it has a more-or-less normal distribution of letters, as opposed to using 'Content here, content here', making it look like readable English. Many desktop publishing packages and web page editors now use Lorem Ipsum as their default model text, and a search for 'lorem ipsum' will uncover many web sites still in their infancy. Various versions have evolved over the years</p>
  <p>The point of using Lorem Ipsum is that it has a more-or-less normal distribution of letters, as opposed to using 'Content here, content here', making it look like readable English. Many desktop publishing packages and web page editors now use Lorem Ipsum</p>
  <span class="btn-pill"><i></i>READ MORE</span>
</section>

<div class="about-frame abs">
  <svg class="abs" width="360" height="436" viewBox="0 0 360 436">
    <path d="M0 60 V0 H60" fill="none" stroke="#6b449b" stroke-width="14"/>
    <path d="M40 0 H320 a40 40 0 0 1 40 40 V396" fill="none" stroke="#c8c8cc" stroke-width="12"/>
    <path d="M0 300 V416 a20 20 0 0 0 20 20 H360 V380" fill="none" stroke="#6b449b" stroke-width="14"/>
  </svg>
  <div class="about-photo" role="img" aria-label="Portrait of the company founder in a dark suit"></div>
</div>

<section class="services abs">
  <h2 class="section-title">OUR <b>SERVICES</b></h2>
  <div class="title-rule"></div>
  <div class="intro">
    <p class="lead"><span class="hl">LUMERA FIELDWORKS</span> It is a long established fact that a reader will be distracted by the readable content of a page when looking at its layout. The point of using Lorem Ipsum is that it has a more-or-less normal distribution of letters</p>
    <p>The point of using Lorem Ipsum is that it has a more-or-less <span class="hl">LUMERA FIELDWORKS</span> normal distribution of letters, as opposed to using 'Content here, content here', making it look like readable English</p>
  </div>
  <span class="slider-arrow" style="left:67px"><svg width="10" height="10" viewBox="0 0 10 10"><path d="M7 1L3 5l4 4" fill="none" stroke="#888" stroke-width="1.6"/></svg></span>
  <span class="slider-arrow" style="left:1093px"><svg width="10" height="10" viewBox="0 0 10 10"><path d="M3 1l4 4-4 4" fill="none" stroke="#888" stroke-width="1.6"/></svg></span>
  <div class="service-row">
    <div class="service-card">
      <svg viewBox="0 0 48 48"><rect x="5" y="9" width="38" height="26" rx="2"/><path d="M16 41h16M24 35v6M18 22l4 4 8-8"/></svg>
      <h3>Cyber Security<br>Services</h3>
      <p>The point of using Lorem Ipsum is that it has point more-or-lessmaking that itlook like readable</p>
    </div>
    <div class="service-card">
      <svg viewBox="0 0 48 48"><path d="M12 5h18l8 8v30H12z"/><path d="M30 5v8h8M18 22h14M18 28h14M18 34h8"/></svg>
      <h3>Managed Security<br>Services</h3>
      <p>The point of using Lorem Ipsum is that it has point more-or-lessmaking that itlook like readable</p>
    </div>
    <div class="service-card is-active">
      <svg viewBox="0 0 48 48"><path d="M24 6c-9 0-15 6-15 14 0 5 3 8 3 12v8h12M24 6c9 0 15 6 15 14 0 5-3 8-3 12v8H24M24 6v34M16 18h8M24 26h8"/></svg>
      <h3>Deep Slight<br>Intelligence</h3>
      <p>The point of using Lorem Ipsum is that it has point more-or-lessmaking that itlook like readable</p>
      <span class="more">READ MORE »</span>
    </div>
    <div class="service-card">
      <svg viewBox="0 0 48 48"><path d="M6 42h36M10 42V30M18 42V22M26 42V26M34 42V16M8 24l10-10 8 6 12-12M32 8h6v6"/></svg>
      <h3>Incident Response<br>Services</h3>
      <p>The point of using Lorem Ipsum is that it has point more-or-lessmaking that itlook like readable</p>
    </div>
    <div class="service-card">
      <svg viewBox="0 0 48 48"><path d="M8 40l18-18M30 8a8 8 0 0 0 10 10l-6 6-10-10zM8 8l8 8M12 18l6-6M30 30l10 10"/></svg>
      <h3>Other<br>Services</h3>
      <p>The point of using Lorem Ipsum is that it has point more-or-lessmaking that itlook like readable</p>
    </div>
  </div>
</section>

<section class="products abs">
  <h2 class="section-title">OUR <b>PRODUCTS</b></h2>
  <div class="title-rule"></div>
  <svg class="product-wheel" width="1200" height="744" viewBox="0 0 1200 744">
    <circle cx="600" cy="410" r="218" fill="none" stroke="#e6e6ea" stroke-width="2"/>
    <circle cx="600" cy="410" r="128" fill="none" stroke="#cfcfd4" stroke-width="14"/>
    <path d="M600 282 A128 128 0 0 1 715 354" fill="none" stroke="#6b449b" stroke-width="14"/>
    <circle cx="600" cy="410" r="104" fill="#fff"/>
    <circle cx="600" cy="410" r="30" fill="#6b449b"/>
    <g fill="#3f3f44">
      <circle cx="600" cy="212" r="40" fill="#6b449b"/>
      <circle cx="750" cy="286" r="40"/>
      <circle cx="802" cy="422" r="40"/>
      <circle cx="750" cy="563" r="40"/>
      <circle cx="600" cy="628" r="40"/>
      <circle cx="446" cy="570" r="40"/>
      <circle cx="390" cy="427" r="40"/>
      <circle cx="446" cy="281" r="40"/>
    </g>
    <g fill="none" stroke="#fff" stroke-width="2.4">
      <path d="M600 196l14 6v10c0 9-6 15-14 18-8-3-14-9-14-18v-10z"/><path d="M594 213l5 5 8-9"/>
      <ellipse cx="750" cy="286" rx="17" ry="10"/><circle cx="750" cy="286" r="5"/>
      <rect x="788" y="410" width="28" height="24" rx="3"/><path d="M795 422h14M802 415v14"/>
      <rect x="736" y="550" width="24" height="28" rx="2"/><circle cx="758" cy="570" r="6"/>
      <path d="M600 612l14 6v10c0 8-6 14-14 16-8-2-14-8-14-16v-10z"/><path d="M592 626h16"/>
      <circle cx="446" cy="570" r="15"/><path d="M431 570h30M446 555c-7 8-7 22 0 30M446 555c7 8 7 22 0 30"/>
      <path d="M378 434h24a7 7 0 0 0 0-14 10 10 0 0 0-19-3 7 7 0 0 0-5 17z"/>
      <path d="M434 275l12-7 12 7v14l-12 7-12-7z"/><path d="M434 275l12 7 12-7M446 282v14"/>
    </g>
  </svg>
  <div class="product-label is-featured" style="left:655px;top:205px">Integrated<br>Cyber Defense</div>
  <div class="product-label" style="left:808px;top:285px">Advanced Threat<br>Protection</div>
  <div class="product-label" style="left:860px;top:410px">Information<br>Protection</div>
  <div class="product-label" style="left:808px;top:570px">Endpoint Security</div>
  <div class="product-label" style="left:655px;top:638px">Email Security</div>
  <div class="product-label" style="left:258px;top:562px">Network Security</div>
  <div class="product-label" style="left:224px;top:420px">Cloud Security</div>
  <div class="product-label" style="left:276px;top:262px;text-align:right">Small Business<br>Products</div>
</section>

<section class="team abs">
  <h2 class="section-title">OUR <b>TEAM</b></h2>
  <div class="title-rule"></div>
  <article class="team-card is-open" style="left:172px">
    <div class="team-photo" role="img" aria-label="Portrait of the marketing manager"></div>
    <h4>Mr. Caleb Renwick</h4>
    <div class="role">Marketing Manager</div>
    <div class="contact"><svg width="14" height="14" viewBox="0 0 24 24" fill="#fff"><path d="M6 2l4 5-2 3a12 12 0 0 0 6 6l3-2 5 4-3 4C10 22 2 14 2 5z"/></svg>555 014 2270</div>
    <div class="contact small"><svg width="13" height="11" viewBox="0 0 24 18" fill="none" stroke="#fff" stroke-width="2"><rect x="1" y="1" width="22" height="16"/><path d="M1 1l11 9 11-9"/></svg>caleb@lumerafieldworks.com</div>
  </article>
  <article class="team-card" style="left:469px">
    <div class="team-photo" role="img" aria-label="Portrait of the chief executive officer"></div>
    <h4>Miss Ilsa Marrow</h4>
    <div class="role">C.E.O.</div>
  </article>
  <article class="team-card" style="left:769px">
    <div class="team-photo" role="img" aria-label="Portrait of the marketing officer"></div>
    <h4>Mr. Tobin Hale</h4>
    <div class="role">Marketing Officer</div>
  </article>
</section>

<footer class="site-footer abs">
  <svg class="footer-band" width="1200" height="500" viewBox="0 0 1200 500">
    <path d="M0 30 Q600 -20 1200 30 V500 H0z" fill="#6b449b"/>
  </svg>
  <div class="brand"><span class="dot"></span>LUMERA FIELDWORKS</div>
  <div class="cta">
    <h2>LET'S GET STARTED</h2>
    <div class="rule"></div>
    <p>Take the first step to growing your business with a FREE consultation and quote.</p>
  </div>
  <div class="footer-cols">
    <div>
      <h5>Contact Details</h5>
      <div class="contact-line"><svg width="12" height="14" viewBox="0 0 24 28" fill="#fff"><path d="M12 0a10 10 0 0 0-10 10c0 8 10 18 10 18s10-10 10-18A10 10 0 0 0 12 0zm0 14a4 4 0 1 1 0-8 4 4 0 0 1 0 8z"/></svg><span><b>LUMERA FIELDWORKS SECURITY</b><br>418 Lantern Row, Suite 210<br>Marlow, TX 77990</span></div>
      <div class="contact-line phone"><svg width="14" height="14" viewBox="0 0 24 24" fill="#fff"><path d="M6 2l4 5-2 3a12 12 0 0 0 6 6l3-2 5 4-3 4C10 22 2 14 2 5z"/></svg>555-014-2270</div>
      <div class="contact-line"><svg width="13" height="11" viewBox="0 0 24 18" fill="none" stroke="#fff" stroke-width="2"><rect x="1" y="1" width="22" height="16"/><path d="M1 1l11 9 11-9"/></svg>hello@lumerafieldworks.com</div>
    </div>
    <div>
      <h5>Quick Links</h5>
      <ul class="quick-links"><li>Home</li><li>About Us</li><li>Our Team</li><li>Our Products</li><li>Services</li><li>Contact</li></ul>
    </div>
  </div>
  <form class="contact-form">
    <div class="field">First Name</div>
    <div class="field">Last Name</div>
    <div class="field">Email</div>
    <div class="field">Phone Number</div>
    <div class="field tall">Message</div>
    <span class="btn-pill"><i></i>SUBMIT</span>
  </form>
  <div class="copyright">
    <span>Copyright © 2018 <b>LumeraFieldworks</b>. All Right Reserved.</span>
    <span class="socials"><span></span><span></span><span></span><span></span></span>
  </div>
</footer>

</body>
</html>
```